Bootstrap Website for Sports Technology Company

Create Bootstrap compatible, HTML and CSS stylesheet-based design templates for typography, forms, buttons, charts, navigation and other interface components for the www.tallow-pinery.com website. All designs should be Responsive CSS and Fluid.
We are transitioning www.tallow-pinery.com from Wordpress to Bootstrap and are looking for a fresh, clean landing page with navigation to other page styles. Official Colors and font are attached. Designer may recommend button styles, menu navigation, header, footer, etc. Please incorporate the graphic elements found on the tallow-pinery.com website.
Page Styles required:
- Landing Page
- Secondary Landing Page
- Five different Page Styles
- small, medium and large buttons
Designers are encouraged to submit the landing page with navigation. We will comment quickly to help with finalizing the design for final selection.
Industry/Entity Type
It Company
Look and feel
Each slider illustrates characteristics of the customer's brand and the style your logo design should communicate.

```html
<!DOCTYPE html>
<html lang="en">
<head>
<meta charset="utf-8">
<title>Tallow Pinery — Landing</title>
<link href="https://fonts.googleapis.com/css2?family=Open+Sans:wght@400;600;700;800&display=swap" rel="stylesheet">
<style>
:root{
  --nav:#1c1c1c;
  --teal:#1e5c5d;
  --teal-dark:#164849;
  --page:#dedede;
  --panel:#ededed;
  --band:#c9c9c9;
  --ink:#555;
  --ink-soft:#888;
  --white:#fff;
  --ribbon:#4a4a4a;
  --field:#fafafa;
}
*{box-sizing:border-box;margin:0;padding:0}
html,body{width:695px;height:1200px;overflow:hidden}
body{background:var(--page);font-family:"Open Sans",Arial,sans-serif;color:var(--ink);position:relative}

.topnav{position:absolute;top:0;left:0;width:695px;height:20px;background:var(--nav);display:flex;align-items:center;padding:0 70px;z-index:3}
.topnav a{color:var(--white);font-size:8px;text-decoration:none;margin-right:18px}
.topnav .search{margin-left:auto;width:84px;height:12px;background:var(--white);border-radius:2px;font-size:6px;color:var(--ink-soft);padding:2px 4px;position:relative}
.topnav .search svg{position:absolute;right:3px;top:2px}

.hero{position:absolute;top:20px;left:0;width:695px;height:305px;background:linear-gradient(180deg,#c9a46a 0%,#e3cf9c 20%,#8fa04a 40%,#3f7a22 65%,#2b5e17 100%)}
.brand{position:absolute;top:26px;left:22px;display:flex;align-items:center;gap:6px;z-index:2}
.brand .mark{width:44px;height:44px;border-radius:50%;background:rgba(255,255,255,.25)}
.brand .name{font-size:17px;font-weight:700;color:var(--teal)}
.hero-text{position:absolute;top:222px;left:0;width:695px;text-align:center;color:var(--white);font-size:17px;line-height:21px;z-index:2}

.features{position:absolute;top:330px;left:42px;width:611px;height:152px;background:var(--white);box-shadow:0 2px 8px rgba(0,0,0,.25);display:flex;justify-content:space-around;align-items:center;padding:0 40px}
.feature{display:flex;align-items:center;gap:6px}
.feature .label{writing-mode:vertical-rl;transform:rotate(180deg);font-size:22px;color:var(--ink-soft)}
.feature .art{width:70px;height:110px;background:linear-gradient(180deg,#555,#8a8a8a)}

.blog{position:absolute;top:482px;left:0;width:695px;height:208px;background:var(--teal);color:var(--white)}
.blog h2{text-align:center;font-size:17px;font-weight:700;margin-top:10px}
.blog .intro{text-align:center;font-size:9px;line-height:13px;width:540px;margin:4px auto 0}
.posts{position:absolute;top:80px;left:70px;width:570px;display:grid;grid-template-columns:1fr 1fr;row-gap:14px;column-gap:30px}
.post{display:flex;gap:8px}
.post .date{flex:none;width:26px;height:26px;border-radius:50%;background:var(--white);color:var(--teal);font-size:11px;font-weight:700;display:flex;align-items:center;justify-content:center}
.post h3{font-size:8px;font-weight:700}
.post p{font-size:7px;line-height:9px;opacity:.85}
.post .meta{font-size:6px;opacity:.7;margin-top:2px}

.shade{position:absolute;top:690px;left:60px;width:575px;height:22px;background:radial-gradient(ellipse at top,rgba(0,0,0,.2),rgba(0,0,0,0) 70%)}
.side-band{position:absolute;top:815px;left:0;width:695px;height:90px;background:var(--band)}
.contact-tab{position:absolute;top:762px;left:555px;width:98px;height:20px;background:var(--panel);font-size:8px;color:var(--ink-soft);text-align:center;line-height:20px;border-radius:3px 3px 0 0}

.contact{position:absolute;top:782px;left:42px;width:611px;height:388px;background:var(--panel);box-shadow:0 1px 5px rgba(0,0,0,.15)}
.contact h2{position:absolute;left:50px;top:14px;font-size:36px;font-weight:800;color:var(--ink);line-height:40px}
.contact .sub{position:absolute;left:50px;top:56px;font-size:19px;font-weight:700;color:var(--ink)}
.form{position:absolute;left:50px;top:93px;width:240px}
.form .field{height:15px;background:var(--field);border:1px solid #cfcfcf;font-size:6px;color:var(--ink-soft);padding:3px 6px;margin-bottom:9px}
.form .area{height:122px}
.submit{position:absolute;left:92px;top:305px;width:96px;height:20px;border-radius:10px;background:#666;color:var(--white);font-size:8px;font-weight:700;text-align:center;line-height:20px}
.ribbon{position:absolute;left:362px;top:84px}
.connect{position:absolute;left:362px;top:152px;font-size:7px;color:var(--ink)}
.socials{display:flex;gap:6px;margin-top:6px}
.socials span{width:20px;height:20px;background:#bbb;border-radius:2px}
.outreach{position:absolute;right:40px;top:212px;text-align:right;font-size:6.5px;line-height:9px;color:var(--ink)}
.outreach h4{font-size:10px;font-weight:700;margin-bottom:3px}
.totop{position:absolute;left:272px;top:350px;width:46px;height:14px;background:#e4e4e4;border:1px solid #ccc;font-size:6px;text-align:center;line-height:12px;color:var(--ink-soft)}
.copy{position:absolute;right:40px;top:355px;font-size:6px;color:var(--ink-soft)}
</style>
</head>
<body>
<nav class="topnav">
  <a href="#">Home</a><a href="#">About</a><a href="#">World</a><a href="#">Golf</a><a href="#">Clubhouse</a>
  <div class="search">Search here
    <svg width="7" height="7" viewBox="0 0 10 10"><circle cx="4" cy="4" r="3" fill="none" stroke="#555" stroke-width="1.5"/><line x1="6.2" y1="6.2" x2="9" y2="9" stroke="#555" stroke-width="1.5"/></svg>
  </div>
</nav>

<header class="hero" role="img" aria-label="Golf ball on a tee over green grass at sunset"></header>
<div class="brand"><span class="mark"></span><span class="name">Tallow Pinery</span></div>
<p class="hero-text">Lorem ipsum dolor sit amet, consectetur adipisicing elit,<br>sed do eiusmod tempor incididunt ut labore</p>

<section class="features">
  <div class="feature"><span class="label">Collect</span><div class="art" role="img" aria-label="Golfer silhouette mid swing"></div></div>
  <div class="feature"><span class="label">Analyze</span><div class="art" role="img" aria-label="Analysis emblem graphic"></div></div>
  <div class="feature"><span class="label">Instruct</span><div class="art" role="img" aria-label="Handheld device sending signal"></div></div>
</section>

<section class="blog">
  <h2>Latest Blog</h2>
  <p class="intro">Nulla vitae elit libero, a pharetra augue. Aenean lacinia bibendum nulla sed consectetur. Aenean lacinia bibendum nulla sed consectetur. Morbi leo risus, porta ac consectetur ac, vestibulum at eros.</p>
  <div class="posts">
    <article class="post"><div class="date">12</div><div><h3>Aenean Adipiscing Etiam Vestibulum</h3><p>Sed porta nisl malesuada magna lorem elit semper mollis. Cras mattis consectetur purus.</p><p class="meta">Journal Photography · 6 Comments</p></div></article>
    <article class="post"><div class="date">13</div><div><h3>Inceptos Purus Etiam Condimentum</h3><p>Aenean leo quam pellentesque ornare sem lacinia quam. Vestibulum id ligula porta felis.</p><p class="meta">Journal Photography · 10 Comments</p></div></article>
    <article class="post"><div class="date">14</div><div><h3>Commodo Sem Inceptos Fusce</h3><p>Duis mollis est non commodo luctus nisi erat porttitor ligula eget lacinia odio sem.</p><p class="meta">Journal Photography · 11 Comments</p></div></article>
    <article class="post"><div class="date">15</div><div><h3>Justo Etiam Elementum Venenatis</h3><p>Integer posuere erat a ante venenatis dapibus posuere velit aliquet donec sed odio.</p><p class="meta">Journal Photography · 8 Comments</p></div></article>
  </div>
</section>
<div class="shade"></div>

<div class="side-band"></div>
<div class="contact-tab">CONTACT ME</div>
<section class="contact">
  <h2>Thank you!</h2>
  <p class="sub">Get in touch with me now.</p>
  <form class="form">
    <div class="field">Your Name</div>
    <div class="field">Your Email Address</div>
    <div class="field">Your Estimated Budget</div>
    <div class="field area">Your Project Description</div>
  </form>
  <div class="submit">SUBMIT NOW</div>
  <svg class="ribbon" width="214" height="44" viewBox="0 0 214 44">
    <polygon points="18,4 214,4 214,34 18,34 2,19" fill="var(--ribbon)"/>
    <polygon points="200,34 214,34 214,42" fill="#2e2e2e"/>
    <text x="112" y="24" text-anchor="middle" font-family="Open Sans, sans-serif" font-size="13" font-weight="700" fill="#fff">Available For Hire</text>
  </svg>
  <div class="connect">Connect with me Via:
    <div class="socials"><span></span><span></span><span></span><span></span></div>
  </div>
  <div class="outreach">
    <h4>Outreach:</h4>
    <p>Pinery Spring Event and Clubhouse Tour 2013</p>
    <p>Pinery Regional Cup Online Launch 2013</p>
    <p>Ready for Tee Off: Three Product Updates</p>
    <p>Pinery Fall Swing Clinic Series 2013</p>
    <p>See more</p>
  </div>
  <div class="totop">GO TO TOP</div>
  <div class="copy">© 2013 www.tallow-pinery.com</div>
</section>
</body>
</html>
```